I need a business card for my original fine art pieces

I would like a business card design including a logo design for a new business in the art world. I am based in the Hunter Valley NSW Australia. I am a contemporary figurative, encaustic and wildlife artist. I would like to be able to upload my email and mobile number to this as well. This design should be one that I can incorporate into banners and flyers etc. Id like to incorporate one of my own images or partial image into the background or somewhere below. My initials are RJ and I would like these used as a logo type. I would like the use of some colour and it to be bright and catchy. The final design should communicate artwork custom made and commissions available.

Overview: Original Fine Artworks for sale, online, art galleries etc, Custom made to order and by commission.

Target market is world wide audience and corporate world

My figurative work is painted using acrylics in a lot of natural ochre colours that reflect the Australian Outback, on canvas, linen, paper or board: My encaustic work is created in a contemporary abstract style using a blow torch and a made with a medium of 100% pure bees wax, Damar resin, mixed media and coloured pigments, applied to Birch board. My wildlife are created using coloured pencil and mixed media on a variety of paper types or board.

```html
<!DOCTYPE html>
<html lang="en">
<head>
<meta charset="utf-8">
<title>Rhea Jansen – Business Cards</title>
<link rel="stylesheet" href="https://fonts.googleapis.com/css2?family=Cinzel:wght@500&family=Source+Sans+3:wght@400;600&display=swap">
<style>
  :root {
    --backdrop: #161616;
    --card-light: #f3f3f3;
    --brand-orange: #fe4200;
    --ink: #1c1c1c;
    --white: #ffffff;
  }
  * { box-sizing: border-box; margin: 0; padding: 0; }
  html, body {
    width: 1200px;
    height: 900px;
    overflow: hidden;
    background: var(--backdrop);
  }
  .canvas {
    position: relative;
    width: 1200px;
    height: 900px;
  }
  .card {
    position: absolute;
    top: 184px;
    height: 490px;
    border-radius: 12px;
    text-align: center;
    font-family: "Source Sans 3", sans-serif;
  }
  .card--front {
    left: 299px;
    width: 301px;
    background: var(--card-light);
    color: var(--ink);
  }
  .card--back {
    left: 645px;
    width: 304px;
    background: var(--brand-orange);
    color: var(--white);
  }
  .brand-mark {
    position: absolute;
    left: 50%;
    transform: translateX(-50%);
    border-radius: 50%;
    display: flex;
    align-items: center;
    justify-content: center;
    font-family: "Source Sans 3", sans-serif;
    font-weight: 600;
    white-space: nowrap;
  }
  .card--front .brand-mark {
    top: 79px;
    width: 144px;
    height: 144px;
    border: 3px solid var(--brand-orange);
    color: var(--brand-orange);
    font-size: 20px;
  }
  .card--back .brand-mark {
    top: 277px;
    width: 106px;
    height: 106px;
    border: 3px solid var(--white);
    color: var(--white);
    font-size: 15px;
  }
  .contact {
    position: absolute;
    top: 261px;
    left: 0;
    right: 0;
    font-size: 14.5px;
    line-height: 17.5px;
  }
  .contact__name {
    color: var(--brand-orange);
    font-weight: 600;
    font-size: 17px;
    line-height: 20px;
  }
  .contact__block { margin-top: 12px; }
  .brand-name {
    position: absolute;
    top: 381px;
    left: 0;
    right: 0;
    font-family: "Cinzel", serif;
    font-weight: 500;
    font-size: 39px;
    letter-spacing: 1px;
    line-height: 42px;
    white-space: nowrap;
  }
  .brand-tagline {
    position: absolute;
    top: 419px;
    left: 0;
    right: 0;
    font-family: "Source Sans 3", sans-serif;
    font-weight: 400;
    font-size: 15.5px;
    letter-spacing: 4.3px;
    line-height: 17px;
    white-space: nowrap;
  }
</style>
</head>
<body>
<main class="canvas">
  <section class="card card--front" aria-label="Card front">
    <div class="brand-mark">Rhea Jansen</div>
    <div class="contact">
      <p class="contact__name">Daniel Hart</p>
      <p class="contact__role">Managing Director</p>
      <div class="contact__block">
        <p>12345, Address Goes Here</p>
        <p>Country Name, 123456.</p>
      </div>
      <div class="contact__block">
        <p>044-123 456 789</p>
        <p>info@webname.com</p>
        <p>www.websitename.com</p>
      </div>
    </div>
  </section>

  <section class="card card--back" aria-label="Card back">
    <div class="brand-mark">Rhea Jansen</div>
    <h1 class="brand-name">Rhea Jansen</h1>
    <p class="brand-tagline">ORIGINAL FINE ARTWORKS</p>
  </section>
</main>
</body>
</html>
```